USB Flash Drive Catalogue

I would like to make a paper catalogue of the products from our Crafterly store. There are currently 209 items on Crafterly. Some would be excluded. The listings have pricing and would need to be organized a bit different but all the information is there.

https://www.crafterly.com/shop/TurboStickHub/items?ref=pagination&page=1

```html
<!DOCTYPE html>
<html lang="en">
<head>
<meta charset="utf-8">
<title>TurboStickHub Product Catalog – Cover</title>
<link href="https://fonts.googleapis.com/css2?family=Montserrat:wght@400;500;600;700;800&display=swap" rel="stylesheet">
<style>
  :root{
    --stage:#d9d9d9;
    --orange:#e5823a;
    --orange-deep:#b9642a;
    --paper:#f4f3f1;
    --ink:#2b2b2b;
    --accent-text:#c9661f;
    --photo-dark:#2f2f31;
    --photo-mid:#4a4744;
  }
  *{box-sizing:border-box;margin:0;padding:0}
  html,body{width:1200px;height:804px;overflow:hidden}
  body{background:var(--stage);font-family:'Montserrat',sans-serif;position:relative}
  .cover{
    position:absolute;left:339px;top:32px;width:523px;height:740px;
    background:var(--orange);overflow:hidden;
    box-shadow:0 6px 20px rgba(0,0,0,.18);
  }
  .cover__shapes{position:absolute;inset:0}
  .title{position:absolute;left:44px;top:118px;color:#fff}
  .title__kicker{font-weight:800;font-size:27px;letter-spacing:.5px;line-height:1}
  .title__main{font-weight:800;font-size:62px;letter-spacing:1px;line-height:.95;margin-top:2px}
  .title__headline{font-weight:600;font-size:15px;letter-spacing:.8px;margin-top:10px}
  .title__body{font-weight:400;font-size:9px;line-height:1.6;margin-top:14px;width:290px;opacity:.95}
  .photo{
    position:absolute;border:4px solid var(--orange-deep);
    background:linear-gradient(135deg,var(--photo-mid),var(--photo-dark));
  }
  .photo--drive-blue{left:124px;top:320px;width:168px;height:124px}
  .photo--drive-wood{left:156px;top:452px;width:168px;height:118px}
  .photo--gift-box{left:302px;top:320px;width:176px;height:158px;
    background:linear-gradient(135deg,#6b5e4e,var(--photo-dark))}
  .brand{position:absolute;left:60px;top:622px;display:flex;align-items:center;gap:10px}
  .brand__dot{width:22px;height:22px;border-radius:50%;background:var(--orange)}
  .brand__name{font-weight:600;font-size:21px;letter-spacing:2px;color:var(--ink)}
  .contact{position:absolute;left:60px;top:690px;font-size:10px;line-height:1.45}
  .contact__email{font-weight:700;color:var(--ink)}
  .contact__web{font-weight:800;color:var(--accent-text)}
</style>
</head>
<body>
  <main class="cover">
    <svg class="cover__shapes" width="523" height="740" viewBox="0 0 523 740" aria-hidden="true">
      <polygon points="0,548 160,492 523,445 523,702" fill="var(--orange-deep)"/>
      <polygon points="0,566 160,500 523,702 523,740 0,740" fill="var(--paper)"/>
    </svg>

    <header class="title">
      <p class="title__kicker">PRODUCT</p>
      <h1 class="title__main">CATALOG</h1>
      <p class="title__headline">YOUR HEADLINE GOES HERE</p>
      <p class="title__body">Your some Sample text here mauris ante tortor adipiscing at porta tempus commodo vel ipsum elementum tellus interdum diam risus.</p>
    </header>

    <div class="photo photo--drive-blue" role="img" aria-label="Blue USB flash drive with matching box on dark wood"></div>
    <div class="photo photo--drive-wood" role="img" aria-label="Engraved wooden USB flash drive on dark wood"></div>
    <div class="photo photo--gift-box" role="img" aria-label="Wooden gift box holding an engraved USB drive"></div>

    <div class="brand">
      <span class="brand__dot"></span>
      <span class="brand__name">TURBOSTICKHUB</span>
    </div>

    <footer class="contact">
      <p class="contact__email">Email: info@turbostickhub.com</p>
      <p class="contact__web">WWW.TURBOSTICKHUB.COM</p>
    </footer>
  </main>
</body>
</html>
```